Valderons Business Card

Business card for philanthropic organization

Industry/Entity Type

Business

Contact Information for Business Card

Need a very ELEGANT, sober, embossed, formal business card... it should transmit CREDIBILITY. Not looking for a "fun card". would like white, grays or black designs.

Font styles to use
Script

Requirements
Must have
• Embossed look

```html
<!DOCTYPE html>
<html lang="en">
<head>
<meta charset="utf-8">
<title>Valderons Business Card</title>
<link href="https://fonts.googleapis.com/css2?family=Lobster&family=Roboto:wght@400;500&display=swap" rel="stylesheet">
<style>
  :root {
    --backdrop: #6b625c;
    --card: #141414;
    --card-edge: #1e1e1e;
    --emboss-dark: #0b0b0b;
    --emboss-light: #3a3a3a;
    --text: #f2f2f2;
    --logo-text: #d9d9d9;
  }
  html, body {
    margin: 0;
    width: 1200px;
    height: 934px;
    overflow: hidden;
    background: var(--backdrop);
  }
  .canvas {
    position: relative;
    width: 1200px;
    height: 934px;
    display: flex;
    align-items: center;
    justify-content: center;
  }
  .business-card {
    position: relative;
    width: 1000px;
    height: 572px;
    background: radial-gradient(ellipse at 40% 30%, var(--card-edge), var(--card) 70%);
    border-radius: 10px;
    box-shadow: 0 18px 40px rgba(0,0,0,0.45);
    font-family: "Roboto", sans-serif;
    color: var(--text);
  }
  .holder-name {
    position: absolute;
    left: 80px;
    top: 270px;
    margin: 0;
    font-family: "Lobster", cursive;
    font-weight: 400;
    font-size: 52px;
    color: var(--emboss-dark);
    text-shadow: -1px -1px 1px var(--emboss-light), 1px 2px 2px rgba(0,0,0,0.9);
  }
  .holder-details {
    position: absolute;
    left: 80px;
    top: 340px;
    margin: 0;
    font-size: 24px;
    line-height: 1.3;
    letter-spacing: 0.3px;
  }
  .holder-role {
    margin-bottom: 22px;
  }
  .brand-mark {
    position: absolute;
    right: 110px;
    top: 180px;
    display: flex;
    align-items: center;
    gap: 14px;
    font-family: "Roboto", sans-serif;
    font-weight: 500;
    font-size: 30px;
    letter-spacing: 2px;
    color: var(--logo-text);
  }
  .brand-dot {
    width: 18px;
    height: 18px;
    border-radius: 50%;
    background: var(--logo-text);
  }
</style>
</head>
<body>
  <div class="canvas">
    <div class="business-card">
      <div class="brand-mark">
        <span class="brand-dot"></span>
        <span>Valderons</span>
      </div>
      <h1 class="holder-name">Mateo Lindero</h1>
      <div class="holder-details">
        <div class="holder-role">Casa Norte Valderons Potentate 2017</div>
        <div class="holder-phone">+(507)-6000-4821</div>
        <div class="holder-email">mlindero@mailbox.com</div>
        <div class="holder-address">P.O. Box 0000-01234 Panama, Republic of Panama</div>
      </div>
    </div>
  </div>
</body>
</html>
```